WP website design (Harrowgate)

We need a wordpress design for an established auction and real estate company based in Florida. The winning design will incorporate a professional color scheme with company logo in a clean layout. The design needs to consider that this will be developed on a responsive theme. Colors are those that will highlight the logo.

Industry/Entity Type

Real Estate

Font styles to use
Serif
Sans Serif

Colors

Designer to choose colors to be used in the design.

Requirements
Must have
• Navigation:
1) Home
2) Auctions
3) Online Auctions
4) About Us
5) Services
6) Real Estate Listings
7) References
8) Contact Us

Colors will be blue (#000066) / red (#B10000) and black or other complementary color. Tagline to be used "Since 1977, Proven Results." Slideshow to be placed in the header or body of home page - please use stock real estate image.

Widgets: 1) Email Sign-up 2) Social media icons for FB and LinkedIn 3) Featured Listings 4) Testimonials 5) Register button

Footer will have smaller company logo, attached logos and contact info:
Phone: (555) 261-0948 Mobile: (555) 718-3062
Email: mirelharrowgate@quellmail.example
Address: 58 E. Tamsin Avenue, Ste 410, Pensacola, FL 32599
Nice to have
• Use of a drop down menu:
Auctions-
1) Upcoming Auctions
2) Past Auctions

```html
<!DOCTYPE html>
<html lang="en">
<head>
<meta charset="utf-8">
<title>Harrowgate Auctions</title>
<link rel="stylesheet" href="https://fonts.googleapis.com/css2?family=Open+Sans:wght@400;600&family=Crimson+Text:wght@400&display=swap">
<style>
:root{
  --red:#b10000;
  --navy:#000066;
  --ink:#2a2a2a;
  --muted:#8a8a8a;
  --line:#d6d6d6;
  --nav:#ececec;
  --page:#e9e9e9;
  --footer:#d2d2d2;
  --white:#ffffff;
}
*{box-sizing:border-box;margin:0;padding:0}
html,body{width:862px;height:1200px;overflow:hidden}
body{position:relative;font-family:"Open Sans",Arial,sans-serif;color:var(--ink);
  background:radial-gradient(ellipse at 50% 40%,#f6f6f6 0%,#e4e4e4 70%,#dcdcdc 100%)}
.abs{position:absolute}

.topbar{left:0;top:0;width:862px;height:24px;background:var(--red)}
.register{left:711px;top:2px;width:53px;height:17px;background:#eeeeee;border:1px solid #bbb;
  font-size:9px;line-height:15px;text-align:center;color:#333}

.upper-band{left:0;top:24px;width:862px;height:388px;background:linear-gradient(#d9d9d9,#cfcfcf)}
.header{left:86px;top:24px;width:689px;height:74px;background:var(--white)}
.brand{left:96px;top:36px;display:flex;align-items:center;gap:12px}
.brand-mark{width:40px;height:40px;background:var(--navy)}
.brand-name{font-size:23px;font-weight:600;color:var(--navy);line-height:1;margin-top:-14px}
.brand-sub{left:154px;top:67px;font-size:11px;letter-spacing:7.5px;font-weight:600;color:var(--navy)}
.signup-input{left:598px;top:55px;width:111px;height:20px;border:1px solid var(--line);
  font-size:9px;color:#aaa;line-height:18px;padding-left:5px;background:#fff}
.signup-btn{left:712px;top:56px;width:52px;height:18px;background:var(--red);color:#fff;
  font-size:9.5px;font-weight:600;text-align:center;line-height:18px}

.nav{left:86px;top:98px;width:689px;height:26px;background:var(--nav);display:flex}
.nav a{display:block;height:26px;line-height:26px;text-align:center;font-size:11px;color:#555;
  text-decoration:none;border-left:1px solid #cfcfcf}
.nav a:first-child{border-left:none}
.dropdown{left:152px;top:124px;width:122px;background:#e4e4e4}
.dropdown div{height:27px;line-height:27px;padding-left:7px;font-size:10.5px;color:#555;border-bottom:1px solid #fff}

.hero{left:86px;top:124px;width:689px;height:288px;
  background:linear-gradient(180deg,#5a95c9 0%,#9cc3e3 35%,#b9ccd4 55%,#4f8a3a 72%,#2f6b2a 100%)}
.caption{left:86px;top:369px;width:689px;height:43px;background:rgba(230,236,230,.72)}
.caption-text{left:96px;top:375px;font-family:"Crimson Text",Georgia,serif;font-size:17px;color:var(--navy)}
.dots{left:728px;top:384px;display:flex;gap:2px}
.dots i{width:7px;height:7px;border-radius:50%;background:var(--navy)}
.dots i:first-child{background:var(--red)}

h2.section{position:absolute;font-weight:400;font-size:16px;color:#333}

.listing{width:192px;height:243px;background:var(--white);border:1px solid var(--line)}
.listing .photo{height:142px}
.listing h3{font-weight:400;font-size:12px;margin:10px 0 0 5px;color:#333}
.listing p{width:165px;font-size:8.8px;line-height:14.5px;color:var(--muted);margin:5px 0 0 5px}
.listing a{display:block;font-size:9px;color:var(--red);margin:4px 0 0 6px;text-decoration:none}

.auction{width:237px;height:86px;background:var(--white);border:1px solid var(--line)}
.auction .thumb{position:absolute;left:6px;top:6px;width:68px;height:73px}
.auction h3{position:absolute;left:89px;top:10px;font-weight:400;font-size:12px;color:#333}
.auction .date{position:absolute;left:89px;top:29px;font-size:9px;color:#444}
.auction p{position:absolute;left:89px;top:47px;width:140px;font-size:8.8px;line-height:12px;color:var(--muted)}

.quote{width:200px;font-size:8.8px;line-height:14.5px;color:var(--muted)}
.quote .mark{position:absolute;left:-12px;top:-5px;font-family:"Crimson Text",Georgia,serif;font-size:16px;line-height:16px;color:var(--navy)}
.quote .client{display:block;color:var(--red)}

.footer{left:0;top:1018px;width:862px;height:154px;background:var(--footer)}
.contact{font-size:11.5px;color:#666;line-height:16px;white-space:nowrap}
.social{left:90px;top:1082px;display:flex;gap:6px}
.social i{width:15px;height:15px;border-radius:2px;background:var(--navy)}
.divider{left:86px;top:1106px;width:689px;height:1px;background:#b8b8b8}
.badge{top:1120px;height:40px;background:#c3c3c3;border-radius:2px}
.bottombar{left:0;top:1172px;width:862px;height:28px;background:var(--red);color:#fff;font-size:8.5px;line-height:28px;padding-left:88px}
</style>
</head>
<body>

<div class="abs topbar"></div>
<div class="abs register">REGISTER</div>

<div class="abs upper-band"></div>
<header class="abs header"></header>
<div class="abs brand"><span class="brand-mark"></span><span class="brand-name">Harrowgate</span></div>
<div class="abs brand-sub">AUCTIONS</div>
<div class="abs signup-input">Signup for our email list</div>
<div class="abs signup-btn">SIGNUP</div>

<nav class="abs nav">
  <a style="width:66px">Home</a>
  <a style="width:74px">Auctions</a>
  <a style="width:108px">Online Auctions</a>
  <a style="width:75px">About Us</a>
  <a style="width:72px">Services</a>
  <a style="width:121px">Real Estate Listings</a>
  <a style="width:84px">References</a>
  <a style="width:89px">Contact Us</a>
</nav>

<div class="abs hero" role="img" aria-label="Stock photo of a resort-style residential complex with towers, palm trees and a pool"></div>
<div class="abs dropdown"><div>Upcoming Auctions</div><div>Past Auctions</div></div>
<div class="abs caption"></div>
<div class="abs caption-text">Since 1977, Proven Results</div>
<div class="abs dots"><i></i><i></i><i></i><i></i></div>

<h2 class="section" style="left:85px;top:430px">Featured Listings</h2>

<div class="abs listing" style="left:86px;top:468px">
  <div class="photo" role="img" aria-label="Photo of a key being handed over in front of an apartment building" style="background:linear-gradient(160deg,#7fb0e0,#c9d4dc 60%,#8a97a6)"></div>
  <h3>Roanoke, VA 24018</h3>
  <p>Aenean sollicitudin, lorem quis bibendum auctor, nisi elit consequat ipsum, nec sagittis sem nibh id elit.</p>
  <a>View this property</a>
</div>
<div class="abs listing" style="left:302px;top:468px">
  <div class="photo" role="img" aria-label="Photo of a happy couple in front of their new house" style="background:linear-gradient(180deg,#9c8a78,#d8d2c8 45%,#6f8f4a)"></div>
  <h3>Pasadena, CA 24018</h3>
  <p>Aenean sollicitudin, lorem quis bibendum auctor, nisi elit consequat ipsum, nec sagittis sem nibh id elit.</p>
  <a>View this property</a>
</div>
<div class="abs listing" style="left:86px;top:734px">
  <div class="photo" role="img" aria-label="Photo of a couple on a house porch" style="background:linear-gradient(180deg,#8a5a40,#c7b6a0 50%,#5f8a3a)"></div>
  <h3>Grrenwood Ave, VA 24018</h3>
  <p>Aenean sollicitudin, lorem quis bibendum auctor, nisi elit consequat ipsum, nec sagittis sem nibh id elit.</p>
  <a>View this property</a>
</div>
<div class="abs listing" style="left:302px;top:734px">
  <div class="photo" role="img" aria-label="Photo of a modern office building under blue sky" style="background:linear-gradient(180deg,#4f86c4,#a9c4de 40%,#d9dde0 75%,#6c8f56)"></div>
  <h3>Roanoke, VA 24018</h3>
  <p>Aenean sollicitudin, lorem quis bibendum auctor, nisi elit consequat ipsum, nec sagittis sem nibh id elit.</p>
  <a>View this property</a>
</div>

<h2 class="section" style="left:537px;top:429px">Upcoming Auctions</h2>

<div class="abs auction" style="left:538px;top:467px">
  <div class="thumb" role="img" aria-label="Photo of a white two-storey house" style="background:linear-gradient(180deg,#a9c8e6,#e3e6e0 55%,#6b8f4c)"></div>
  <h3>Roanoke, VA 24018</h3><div class="date">05/24/18 at 6:00 AM EDT</div>
  <p>Aenean sollicitudin, lorem quis bibendum auctor, nisi elit</p>
</div>
<div class="abs auction" style="left:538px;top:569px">
  <div class="thumb" role="img" aria-label="Photo of a red-roofed brick house" style="background:linear-gradient(180deg,#9cc2e8,#c0603a 45%,#d6b89a 70%,#5f8a3a)"></div>
  <h3>Roanoke, VA 24018</h3><div class="date">05/24/18 at 6:00 AM EDT</div>
  <p>Aenean sollicitudin, lorem quis bibendum auctor, nisi elit</p>
</div>
<div class="abs auction" style="left:538px;top:671px">
  <div class="thumb" role="img" aria-label="Photo of a couple looking at a house from behind" style="background:linear-gradient(180deg,#b8c6d6,#8e96a2 50%,#4c4a48)"></div>
  <h3>Roanoke, VA 24018</h3><div class="date">05/24/18 at 6:00 AM EDT</div>
  <p>Aenean sollicitudin, lorem quis bibendum auctor, nisi elit</p>
</div>

<h2 class="section" style="left:538px;top:776px">Testimonials</h2>

<div class="abs quote" style="left:555px;top:811px"><span class="mark">“</span>Aenean sollicitudin, lorem quis bibendum auctor, nisi elit consequat ipsum, nec sagittis<span class="client">Client Name Here</span></div>
<div class="abs quote" style="left:555px;top:868px"><span class="mark">“</span>Aenean sollicitudin, lorem quis bibendum auctor, nisi elit consequat ipsum, nec sagittis<span class="client">Client Name Here</span></div>
<div class="abs quote" style="left:555px;top:928px"><span class="mark">“</span>Aenean sollicitudin, lorem quis bibendum auctor, nisi elit consequat ipsum, nec sagittis<span class="client">Client Name Here</span></div>

<footer class="abs footer"></footer>
<h2 class="section" style="left:86px;top:1022px">Get In Touch With Us</h2>
<div class="abs contact" style="left:87px;top:1057px">Address:&nbsp; 58 E. Tamsin Avenue, Ste 410, Pensacola, FL 32599</div>
<div class="abs contact" style="left:431px;top:1057px">Phone: (555) 261-0948<br>Mobile: (555) 718-3062</div>
<div class="abs contact" style="right:87px;top:1057px;font-size:10px">Email:&nbsp; mirelharrowgate@quellmail.example</div>
<div class="abs social"><i aria-label="Social profile link"></i><i aria-label="Professional network profile link"></i></div>
<div class="abs divider"></div>

<div class="abs badge" style="left:88px;width:60px" role="img" aria-label="Partner association badge"></div>
<div class="abs badge" style="left:169px;width:36px" role="img" aria-label="Partner association badge"></div>
<div class="abs badge" style="left:233px;width:148px" role="img" aria-label="Partner association badge"></div>
<div class="abs badge" style="left:398px;width:78px" role="img" aria-label="Partner association badge"></div>
<div class="abs badge" style="left:519px;width:126px;height:30px;top:1125px" role="img" aria-label="Partner association badge"></div>
<div class="abs badge" style="left:669px;width:104px;height:36px;top:1122px" role="img" aria-label="Certification badge"></div>

<div class="abs bottombar">Copyright 2014. All rights reserved</div>

</body>
</html>
```